Business Cards Needed for Innovative Healthcare Marketing Company

We are a marketing company focused on healthcare. Our company is all about rebranding yourself renewing your image and generating results. The phoenix stands for "reborn" or "rising" which we provide new brands for our clients we take their old brands and renew it with creativity and innovation. I am looking for a business card with color dimension. I have attached an example of a card I think has the look and feel of what I am trying to accomplish. I like that the card example has black and grey font colors, I like the font placement and the small logo, I really like the use of the colors on the right those are the colors of my logo. My logo is phoenix so maybe incorporating flames similar to that design. I would like the back a solid color maybe red with an opaque version of the logo and website. As a marketing company I am always open to creative liberty!

Target Market(s)

Doctors and business professionals.

Industry/Entity Type

Marketing

Contact Information for Business Card

Valcorne Health Care Marketing
Marla Tenwick- CEO
#(512)638-2974
email-marla@valcorne.com
website- valcorne.com

Font styles to use
Sans Serif

Colors
ec1f27
f37122
ffc214
fbed22
fbf289
f04a50

Requirements
Must have
• The logo and required information
Nice to have
• icons by the information
Should not have
• child like font

```html
<!DOCTYPE html>
<html lang="en">
<head>
<meta charset="utf-8">
<title>Valcorne Health Care Marketing – Business Cards</title>
<link rel="stylesheet" href="https://fonts.googleapis.com/css2?family=Raleway:wght@200;300;400&family=Roboto+Slab:wght@400;700&display=swap">
<style>
  :root {
    --canvas: #eee8e2;
    --back-light: #86303c;
    --back-dark: #2e080d;
    --brand-red: #a93226;
    --accent-red: #c0392b;
    --flame-yellow: #ffc214;
    --paper: #ffffff;
    --ink-light: #ffffff;
    --ink-muted: #8a8f96;
    --ink-soft: #e8c9c4;
  }
  * { margin: 0; padding: 0; box-sizing: border-box; }
  html, body { width: 1200px; height: 913px; overflow: hidden; background: var(--canvas); }
  .canvas { position: relative; width: 1200px; height: 913px; }

  .card {
    position: absolute;
    width: 560px;
    height: 320px;
    border-radius: 4px;
    overflow: hidden;
    box-shadow: 0 18px 40px rgba(60, 30, 20, 0.28);
  }

  /* Back of card */
  .card-back {
    left: 60px; top: 110px;
    background: radial-gradient(ellipse at 65% 15%, var(--back-light) 0%, #5e1621 45%, var(--back-dark) 100%);
  }
  .card-back .mark-circle {
    position: absolute; left: 70px; top: 90px;
    width: 140px; height: 140px; border-radius: 50%;
    background: rgba(20, 4, 6, 0.45);
  }
  .card-back .wordmark {
    position: absolute; left: 250px; top: 92px;
    color: var(--ink-light);
    font-family: "Raleway", sans-serif; font-weight: 200;
    font-size: 54px; letter-spacing: 2px; line-height: 1;
  }
  .card-back .tagline {
    position: absolute; left: 252px; top: 160px; width: 270px;
    border-top: 1px solid rgba(255,255,255,0.7);
    padding-top: 6px;
    color: var(--ink-light);
    font-family: "Raleway", sans-serif; font-weight: 300;
    font-size: 15px; letter-spacing: 1px;
  }
  .card-back .web {
    position: absolute; left: 300px; top: 222px;
    color: var(--ink-soft);
    font-family: "Roboto Slab", serif; font-size: 20px;
  }
  .card-back .web .domain { color: var(--accent-red); }

  /* Front of card */
  .card-front { left: 580px; top: 480px; background: var(--paper); }
  .card-front svg.bands { position: absolute; inset: 0; }
  .logo-block {
    position: absolute; left: 40px; top: 80px; width: 250px;
    text-align: center;
  }
  .logo-block .mark-circle {
    width: 90px; height: 90px; border-radius: 50%;
    background: var(--brand-red); margin: 0 auto 14px;
  }
  .logo-block .wordmark {
    color: var(--brand-red);
    font-family: "Raleway", sans-serif; font-weight: 300;
    font-size: 34px; letter-spacing: 1px; line-height: 1;
  }
  .logo-block .tagline {
    display: inline-block; margin-top: 4px; padding-top: 3px;
    border-top: 1px solid var(--brand-red);
    color: var(--brand-red);
    font-family: "Raleway", sans-serif; font-weight: 300;
    font-size: 9.5px; letter-spacing: 0.5px;
  }
  .contact-block {
    position: absolute; left: 400px; top: 88px;
    color: var(--ink-light);
    font-family: "Roboto Slab", serif;
  }
  .contact-block .name { font-size: 20px; font-weight: 400; white-space: nowrap; }
  .contact-block .name b { font-weight: 700; }
  .contact-block .role { color: var(--ink-muted); font-size: 14px; margin-bottom: 14px; }
  .contact-list { list-style: none; }
  .contact-list li {
    display: flex; align-items: center; gap: 8px;
    font-size: 13px; margin-bottom: 5px; white-space: nowrap;
  }
  .contact-list svg { width: 16px; height: 16px; flex: none; }
</style>
</head>
<body>
<main class="canvas">

  <section class="card card-back" aria-label="Business card back">
    <div class="mark-circle"></div>
    <div class="wordmark">VALCORNE</div>
    <div class="tagline">HEALTHCARE MARKETING</div>
    <div class="web">www.<span class="domain">valcorne</span>.com</div>
  </section>

  <section class="card card-front" aria-label="Business card front">
    <svg class="bands" width="560" height="320" viewBox="0 0 560 320">
      <path d="M300,0 C370,70 395,200 388,320 L560,320 L560,0 Z" fill="var(--brand-red)"/>
      <path d="M250,0 C320,50 365,130 384,250 C360,150 325,70 285,0 Z" fill="var(--flame-yellow)"/>
    </svg>

    <div class="logo-block">
      <div class="mark-circle"></div>
      <div class="wordmark">VALCORNE</div>
      <div class="tagline">HEALTHCARE MARKETING</div>
    </div>

    <div class="contact-block">
      <div class="name">Marla <b>TENWICK</b></div>
      <div class="role">CEO</div>
      <ul class="contact-list">
        <li>
          <svg viewBox="0 0 16 16"><circle cx="8" cy="8" r="8" fill="#fff"/><path d="M5.2,4.2 l1.5,1.6 -0.8,1 c0.6,1.3 1.3,2 2.6,2.6 l1-0.8 1.6,1.5 -1,1.3 C7.3,11.2 4.8,8.7 3.9,5.2 Z" fill="var(--brand-red)"/></svg>
          (512) 638-2974
        </li>
        <li>
          <svg viewBox="0 0 16 16"><circle cx="8" cy="8" r="8" fill="#fff"/><rect x="4" y="5.3" width="8" height="5.4" fill="var(--brand-red)"/><path d="M4,5.3 L8,8.5 L12,5.3" stroke="#fff" stroke-width="0.9" fill="none"/></svg>
          marla@valcorne.com
        </li>
        <li>
          <svg viewBox="0 0 16 16"><circle cx="8" cy="8" r="8" fill="#fff"/><circle cx="8" cy="8" r="4.5" fill="none" stroke="var(--brand-red)" stroke-width="1"/><ellipse cx="8" cy="8" rx="2" ry="4.5" fill="none" stroke="var(--brand-red)" stroke-width="1"/><line x1="3.5" y1="8" x2="12.5" y2="8" stroke="var(--brand-red)" stroke-width="1"/></svg>
          valcorne.com
        </li>
      </ul>
    </div>
  </section>

</main>
</body>
</html>
```